NZ First of it's kind solutions directory and marketplace for busy Mums needs a business card design

We need a business card design for our new nationwide business in NZ (long term plans to go global). We provide solutions to the everyday challenges that busy Mums face by connecting them with quality communities and suppliers of carefully selected, relevant products and services. We sell direct via our online marketplace. The final design should communicate our values of inclusivity, quality and smart solutions. Colours should incorporate our logo colour palette of #477077 and #6ba8b2. Our website is at https://www.brightnestmums.example

Target Market(s)

busy Mums, Age 28 – 50, female, income over $100K, location main centres NZ primarily but NZ wide. Is likely juggling work or career with a young family. Probably had hobbies which have fallen by the wayside.
-Wants to succeed in her chosen career without compromising on family life
-to successfully juggle her career without feeling like she is compromising her children
- Is time poor, something always has to give and it’s generally her health (she’ll stay up late, get stressed)
- probably ex corporate or professional career. Has discretional income

Industry/Entity Type

Business

Contact Information for Business Card

Lena Forbisher, Founder, BrightNestMums.example (Strapline Tap; Gather; Sorted), 47 Kowhai Terrace, Ellerslie, Auckland 1051, New Zealand. Mob: 021 483 517 Ph: +64 (0)9 571 4860

Font styles to use
Other font styles liked:
• Raleway, and/or Architects Daughter

Colors
00a990
33b8a4
86cfc6
cfeae6

Requirements
Must have
• the above details, streamline. the logo and colours associated with those logos
Should not have
• foil or metallic colours

```html
<!DOCTYPE html>
<html lang="en">
<head>
<meta charset="utf-8">
<title>BrightNestMums – Business Card</title>
<link rel="stylesheet" href="https://fonts.googleapis.com/css2?family=Architects+Daughter&family=Raleway:wght@500;600;700&display=swap">
<style>
  :root {
    --teal-brand: #477077;
    --teal-light: #6ba8b2;
    --teal-band: #5393a0;
    --teal-deep: #356367;
    --teal-ink: #2e5459;
    --card-white: #f7f8f8;
    --text-grey: #3d4444;
    --backdrop: #e6eaeb;
  }
  * { box-sizing: border-box; margin: 0; padding: 0; }
  html, body {
    width: 1200px; height: 800px; overflow: hidden;
    background: var(--backdrop);
    font-family: "Raleway", Arial, sans-serif;
  }
  .stage { position: relative; width: 1200px; height: 800px; }

  .card {
    position: absolute; top: 250px;
    width: 525px; height: 300px;
    background: var(--card-white);
    border-radius: 3px;
    overflow: hidden;
    box-shadow: 0 6px 18px rgba(0,0,0,0.12);
  }
  .card svg.card-shapes { position: absolute; inset: 0; width: 100%; height: 100%; }

  /* Contact side */
  .card--contact { left: 50px; }
  .contact-title {
    position: absolute; top: 34px; right: 40px;
    color: #fff; font-weight: 700; font-size: 13px; letter-spacing: 2px;
  }
  .contact-name {
    position: absolute; top: 118px; left: 36px;
    color: var(--teal-ink); font-weight: 700; font-size: 25px; letter-spacing: 0.5px;
    text-transform: uppercase;
  }
  .contact-phones {
    position: absolute; top: 226px; left: 36px;
    color: var(--text-grey); font-size: 13.5px; font-weight: 500; line-height: 1.55;
  }
  .contact-divider {
    position: absolute; left: 270px; top: 192px;
    width: 2px; height: 74px; background: var(--text-grey);
  }
  .contact-address {
    position: absolute; top: 196px; left: 290px;
    color: var(--text-grey); font-size: 13.5px; font-weight: 500; line-height: 1.55;
  }

  /* Brand side */
  .card--brand { left: 625px; }
  .brand-lockup {
    position: absolute; top: 70px; left: 0; right: 0;
    display: flex; flex-direction: column; align-items: center;
  }
  .brand-row { display: flex; align-items: center; gap: 12px; }
  .brand-dot {
    width: 34px; height: 34px; border-radius: 50%;
    background: var(--teal-brand);
  }
  .brand-name {
    color: var(--teal-brand); font-weight: 700; font-size: 40px; letter-spacing: -0.5px;
  }
  .brand-strapline {
    margin-top: 4px; margin-left: 46px;
    color: var(--text-grey);
    font-family: "Architects Daughter", "Comic Sans MS", cursive;
    font-size: 21px; letter-spacing: 1px;
  }
  .brand-url {
    position: absolute; bottom: 38px; left: 0; right: 0; text-align: center;
    color: #fff; font-weight: 600; font-size: 18px; letter-spacing: 2px;
  }
</style>
</head>
<body>
<main class="stage">

  <section class="card card--contact" aria-label="Contact side">
    <svg class="card-shapes" viewBox="0 0 525 300" preserveAspectRatio="none" aria-hidden="true">
      <path d="M0 0 H525 V88 C420 92 330 112 262 150 C200 185 110 208 0 208 Z" fill="var(--teal-band)"/>
      <path d="M525 94 C430 100 350 118 290 148 C370 118 450 108 525 110 Z" fill="#ffffff"/>
      <path d="M525 112 C450 112 390 122 330 142 C400 128 460 126 525 130 Z" fill="var(--teal-deep)"/>
      <path d="M0 214 C90 214 170 202 225 178 C170 210 90 228 0 230 Z" fill="var(--teal-band)"/>
    </svg>
    <p class="contact-title">FOUNDER</p>
    <h1 class="contact-name">Lena Forbisher</h1>
    <p class="contact-phones">Mob: 021 483 517<br>Ph: +64 (0)9 571 4860</p>
    <div class="contact-divider"></div>
    <p class="contact-address">47 Kowhai Terrace, Ellerslie<br>Auckland 1051, New Zealand</p>
  </section>

  <section class="card card--brand" aria-label="Brand side">
    <svg class="card-shapes" viewBox="0 0 525 300" preserveAspectRatio="none" aria-hidden="true">
      <path d="M0 178 C110 160 210 168 285 196 C360 224 445 222 525 196 V300 H0 Z" fill="var(--teal-deep)"/>
      <path d="M0 170 C110 150 215 158 290 186 C220 164 110 160 0 176 Z" fill="var(--teal-deep)"/>
      <path d="M525 168 C470 200 400 210 330 206 C410 220 475 214 525 186 Z" fill="var(--teal-light)"/>
    </svg>
    <div class="brand-lockup">
      <div class="brand-row">
        <span class="brand-dot"></span>
        <span class="brand-name">BrightNestMums</span>
      </div>
      <p class="brand-strapline">Tap - Gather - Sorted</p>
    </div>
    <p class="brand-url">www.brightnestmums.example</p>
  </section>

</main>
</body>
</html>
```